Web Design Project

Update to the following web page.

www.velbrontadvisory.com

We would like a full screen website, similar to the ones found here. http://www.pixelorbit.com/websites/fullscreen/

We also really like this site
http://lumenfold.com/

We would like new images and graphics.

Menu should be
1. Audit Defense
2. Education
3. Consulting
4. Outsourcing
5. Our Team
6. Store
7. Contact Us

Incorporate our new logo and colors. File is attached. The blue logo.

We want to add this tag line: "A passion for compliance through homecare and hospice training, education, and consulting."

Target Market(s)

Home Health Care Companies

Industry/Entity Type

Defense

Requirements
Must have
• Display our contact information in header and footer.

```html
<!DOCTYPE html>
<html lang="en">
<head>
<meta charset="utf-8">
<title>Velbront Advisory</title>
<link rel="stylesheet" href="https://fonts.googleapis.com/css2?family=Oswald:wght@500&family=Source+Sans+3:wght@300;400;600&display=swap">
<style>
:root{
  --navy:#1f3d6b;
  --navy-dark:#16325c;
  --steel:#2a4a7a;
  --text:#2d3e5c;
  --muted:#4a5568;
  --gold:#f5b800;
  --gold-dark:#e29f00;
  --footer:#eef2f8;
  --white:#fff;
}
*{margin:0;padding:0;box-sizing:border-box}
html,body{width:1036px;height:1200px;overflow:hidden;background:var(--white)}
body{font-family:"Source Sans 3",sans-serif;color:var(--text);position:relative}
.site-header{height:110px;position:relative}
.brand{position:absolute;left:40px;top:20px;display:flex;align-items:center;gap:16px}
.brand-mark{width:54px;height:54px;background:var(--steel)}
.brand-rule{width:2px;height:74px;background:var(--navy-dark)}
.brand-name{font-size:30px;font-weight:300;color:#4d6d99;letter-spacing:.5px;line-height:1}
.brand-sub{font-size:8px;letter-spacing:9px;color:#6b7f9c;margin-top:6px}
.contact{position:absolute;left:811px;top:22px;font-size:15px;line-height:21px;color:var(--text);font-weight:300;font-style:normal}
.contact .phone{font-size:20px;font-weight:400;margin-top:4px}
.main-nav{position:absolute;top:110px;left:0;width:1036px;height:47px;background:linear-gradient(var(--steel),var(--navy-dark))}
.main-nav ul{list-style:none;display:flex;align-items:center;height:47px;padding-left:30px}
.main-nav li{font-family:"Oswald",sans-serif;font-weight:500;font-size:17px;color:var(--white);padding:0 17px;border-left:1px solid rgba(255,255,255,.35);line-height:18px;white-space:nowrap}
.main-nav li:first-child{border-left:none}
.social{position:absolute;right:0;top:0;width:171px;height:47px;background:var(--navy);clip-path:polygon(14px 0,100% 0,100% 100%,0 100%);display:flex;align-items:center;gap:10px;padding-left:44px}
.social span{width:20px;height:20px;border-radius:50%;background:var(--white)}
.hero{position:absolute;top:157px;left:0;width:1036px;height:489px;background:linear-gradient(120deg,#e8f0f8 0%,#9fc4e8 25%,#1d5fc0 50%,#2c7ad6 70%,#cfe2f4 100%)}
.hero-arrow{position:absolute;top:180px;width:27px;height:94px;background:var(--navy-dark);display:flex;align-items:center;justify-content:center}
.hero-arrow.prev{left:0}.hero-arrow.next{right:0}
.hero-copy{position:absolute;left:497px;top:217px;width:520px}
.hero-copy h1{font-family:"Oswald",sans-serif;font-weight:500;font-size:32px;line-height:42px;color:var(--white);text-transform:uppercase;text-shadow:0 2px 4px rgba(0,0,0,.3);white-space:nowrap}
.btn-gold{display:inline-block;margin-top:10px;background:linear-gradient(var(--gold),var(--gold-dark));color:var(--navy-dark);font-family:"Oswald",sans-serif;font-weight:500;font-size:14px;padding:8px 17px;border-radius:3px}
.intro{position:absolute;top:686px;left:0;width:1036px;text-align:center}
.intro h2{font-size:28px;font-weight:300;color:var(--navy);letter-spacing:-.3px}
.intro h2 strong{font-weight:600}
.intro p{width:720px;margin:12px auto 0;font-size:14.5px;line-height:22.5px;color:var(--muted)}
.cards{position:absolute;top:844px;left:68px;display:flex;gap:22px}
.card{width:282px;height:158px;position:relative;border:1px solid #d5dbe4}
.card-photo{position:absolute;inset:0}
.card-label{position:absolute;left:0;bottom:0;width:100%;height:36px;background:var(--steel);display:flex;align-items:center;justify-content:space-between;padding-left:18px;font-family:"Oswald",sans-serif;font-weight:500;font-size:18px;color:var(--white)}
.card-label i{width:34px;height:36px;background:var(--navy-dark);display:flex;align-items:center;justify-content:center}
.play{position:absolute;left:121px;top:59px;width:40px;height:40px;border-radius:50%;background:#222;display:flex;align-items:center;justify-content:center}
.site-footer{position:absolute;top:1062px;left:0;width:1036px;height:138px;background:linear-gradient(var(--footer),#fbfcfe);border-top:1px solid #dde3ec}
.footer-links{position:absolute;left:50px;top:33px;font-size:13.5px;color:var(--navy)}
.footer-links span{color:#8090a8;margin:0 4px}
.copyright{position:absolute;left:53px;top:72px;font-size:11px;color:var(--muted)}
.site-footer .contact{left:799px;top:30px}
</style>
</head>
<body>
<header class="site-header">
  <div class="brand">
    <div class="brand-mark"></div>
    <div class="brand-rule"></div>
    <div>
      <div class="brand-name">VELBRONT</div>
      <div class="brand-sub">ADVISORY</div>
    </div>
  </div>
  <address class="contact">
    450 Harlow Avenue Suite 210<br>Bramwell, MI, 48120
    <div class="phone">(555) 318-4402</div>
  </address>
</header>
<nav class="main-nav">
  <ul>
    <li>AUDIT DEFENSE</li><li>EDUCATION</li><li>CONSULTING</li><li>OUTSOURCING</li><li>OUR TEAM</li><li>STORE</li><li>CONTACT US</li>
  </ul>
  <div class="social"><span></span><span></span><span></span></div>
</nav>
<section class="hero">
  <div role="img" aria-label="Upward view of a modern glass office tower and control tower against a blue sky" style="position:absolute;inset:0"></div>
  <div class="hero-arrow prev"><svg width="12" height="26" viewBox="0 0 12 26"><path d="M10 2 2 13l8 11" fill="none" stroke="#fff" stroke-width="2"/></svg></div>
  <div class="hero-arrow next"><svg width="12" height="26" viewBox="0 0 12 26"><path d="M2 2l8 11-8 11" fill="none" stroke="#fff" stroke-width="2"/></svg></div>
  <div class="hero-copy">
    <h1>A passion for compliance through<br>homecare and hospice training,<br>education, and consulting.</h1>
    <span class="btn-gold">SEVICES WE PROVIDE</span>
  </div>
</section>
<section class="intro">
  <h2>GET IT DONE RIGHT THE FIRST TIME WITH <strong>VELBRONT &amp; ASSOCIATES!</strong></h2>
  <p>With over 100 years of combined experience in home health care, we have compiled a very strong team of consultants to meet any challenge home health agencies may face today! We are committed to providing the highest quality consulting services to our clients!</p>
</section>
<section class="cards">
  <div class="card">
    <div class="card-photo" role="img" aria-label="Business team meeting around a table with a laptop" style="background:linear-gradient(135deg,#eef1f5,#c9d2de 60%,#f3f4f6)"></div>
    <div class="play"><svg width="14" height="16" viewBox="0 0 14 16"><path d="M2 1l11 7-11 7z" fill="#fff"/></svg></div>
  </div>
  <div class="card">
    <div class="card-photo" role="img" aria-label="Elderly patient speaking with a nurse" style="background:linear-gradient(135deg,#eef0f3,#b9c7d9 55%,#e7dcd2)"></div>
    <div class="card-label">SERVICES WE PROVIDE<i><svg width="10" height="14" viewBox="0 0 10 14"><path d="M1 1l8 6-8 6z" fill="#fff"/></svg></i></div>
  </div>
  <div class="card">
    <div class="card-photo" role="img" aria-label="Consultants reviewing documents together" style="background:linear-gradient(135deg,#3a3f4a,#8a93a3 50%,#d9d3cc)"></div>
    <div class="card-label">WHAT WE DO<i><svg width="10" height="14" viewBox="0 0 10 14"><path d="M1 1l8 6-8 6z" fill="#fff"/></svg></i></div>
  </div>
</section>
<footer class="site-footer">
  <div class="footer-links">Home<span>/</span>Seminars<span>/</span>Services<span>/</span>Our Team<span>/</span>Contact Us<span>/</span>Resources<span>/</span>Store<span>/</span>Coding</div>
  <div class="copyright">© 2013 Company Name.&nbsp; All right reserved. Term of Use</div>
  <address class="contact">
    450 Harlow Avenue Suite 210<br>Bramwell, MI, 48120
    <div class="phone">(555) 318-4402</div>
  </address>
</footer>
</body>
</html>
```